To design a look and feel for a website. The company offers technical services to governemtns and public bodies. It does NOT market to the public.

The core business is GIS (Geographic Information Systems)

The site needs to be clean and simple, The current version is available here: www.velda-maps.ie

Thanks for your interest in our project

Target Market(s)

Goverment agencies and public bodies in the EU, buying through the public procurerment process

Requirements
Should not have
• corny graphics of hands holding globes or sateliites please.

```html
<!DOCTYPE html>
<html lang="en">
<head>
<meta charset="utf-8">
<title>The Velda Group – Information Expertise</title>
<link rel="stylesheet" href="https://fonts.googleapis.com/css2?family=Roboto:ital,wght@0,300;0,400;0,500;0,700;1,400;1,500&family=Noticia+Text:wght@700&display=swap">
<style>
:root{
  --navy:#233f7a;
  --lilac:#7b7dbb;
  --text:#333;
  --panel:#f2f2f2;
  --white:#fff;
}
*{box-sizing:border-box;margin:0;padding:0}
html,body{width:1167px;height:1200px;overflow:hidden}
body{position:relative;font-family:'Roboto',sans-serif;color:var(--text);background:var(--white)}
.abs{position:absolute}

/* top bar */
.topbar{left:0;top:0;width:1167px;height:28px;background:var(--navy)}
.search{left:707px;top:5px;width:192px;height:18px;background:var(--white);border:1px solid #ccd;font:italic 10px 'Roboto',sans-serif;color:#999;padding:3px 5px}
.search svg{position:absolute;right:5px;top:3px}
.contact-us{left:914px;top:0;width:87px;height:28px;background:var(--lilac);color:var(--white);font:500 11.5px 'Roboto',sans-serif;display:flex;align-items:center;justify-content:center}

/* header */
.brand{left:167px;top:84px;display:flex;align-items:center;gap:8px;font:500 22px 'Roboto',sans-serif;color:var(--navy);white-space:nowrap}
.brand i{display:inline-block;width:12px;height:12px;border-radius:50%;background:var(--lilac)}

.nav-item{top:90px;width:80px;text-align:center;font:500 12.5px 'Roboto',sans-serif;color:#2a2a2a}
.nav-item svg{display:block;margin:0 auto 6px;height:28px}
.nav-item.active{color:var(--navy)}
.nav-divider{top:92px;width:1px;height:58px;background:#e2e2e2}
.nav-underline{left:362px;top:161px;width:61px;height:3px;background:var(--navy)}
.call{left:808px;top:100px;width:194px;height:42px;background:var(--lilac);border-radius:3px;color:var(--white);font:400 15px 'Roboto',sans-serif;display:flex;align-items:center;justify-content:center;gap:8px}
.call b{font-weight:500}

/* hero */
.hero{left:0;top:164px;width:1167px;height:412px;background:linear-gradient(100deg,#8a3a0c 0%,#d9700f 30%,#e38a12 50%,#6a3206 75%,#1d1208 100%)}
.hero-caption{left:0;top:493px;width:1167px;height:83px;background:rgba(0,0,0,.72);color:var(--white);font:700 25px/36px 'Noticia Text',serif;text-align:center;padding-top:5px;text-shadow:1px 2px 2px #000}
.hero-arrow{top:322px;width:45px;height:45px;border-radius:50%;background:rgba(0,0,0,.45);display:flex;align-items:center;justify-content:center}

/* content */
.content{left:0;top:576px;width:1167px;height:406px;background:var(--panel)}
.col-title{top:608px;font:400 21px 'Roboto',sans-serif;color:#444;white-space:nowrap}
.col-title span{color:var(--navy)}
.col-rule{top:643px;height:1px;background:#bbb}
.col-rule::after{content:"";position:absolute;right:0;top:0;width:45px;height:1px;background:#ddd}
.copy{top:656px;font:400 11.6px/17px 'Roboto',sans-serif;letter-spacing:.15px;color:#333}
.ticks{list-style:none;margin-top:1px}
.ticks li{font-size:12.3px;line-height:19px;letter-spacing:.2px;display:flex;align-items:center;gap:6px}
.more{top:798px;font:italic 500 11px 'Roboto',sans-serif;color:var(--navy);text-decoration:underline}
.news{left:771px;width:231px;display:flex;gap:11px}
.news .date{width:37px;height:37px;background:var(--navy);color:var(--white);text-align:center;flex:none}
.news .date .m{background:var(--lilac);font:500 10px/13px 'Roboto',sans-serif}
.news .date .d{font:500 14px/24px 'Roboto',sans-serif}
.news p{font:400 10.5px/16.5px 'Roboto',sans-serif;letter-spacing:.5px;color:#555}

.dotted{left:167px;width:835px;border-top:1px dashed #bbb}
.clients-label{left:169px;top:886px;font:italic 500 17px 'Roboto',sans-serif;color:#444}
.client{top:870px;height:60px;display:flex;align-items:center;justify-content:center;gap:8px;font:700 19px 'Roboto',sans-serif;color:var(--navy);white-space:nowrap}
.client i{display:inline-block;width:16px;height:16px;border-radius:50%;background:var(--navy)}

/* footer */
.footer{left:0;top:982px;width:1167px;height:175px;background:var(--navy)}
.foot-title{top:1001px;font:400 17.5px 'Roboto',sans-serif;color:var(--white);display:flex;align-items:center;gap:7px}
.foot-list{list-style:none;color:var(--white);font:400 12.3px 'Roboto',sans-serif}
.foot-list li{display:flex;align-items:center;gap:8px}
.foot-list li::before{content:"";width:5px;height:5px;background:var(--white);border-radius:1px}
.foot-divider{top:1000px;width:1px;height:135px;background:rgba(255,255,255,.25)}
.foot-note{left:539px;top:1044px;width:210px;font:400 11.7px/15.5px 'Roboto',sans-serif;color:var(--white);letter-spacing:.2px}
.email{left:539px;top:1079px;width:184px;height:23px;background:var(--white);border-radius:2px;font:italic 10.5px 'Roboto',sans-serif;color:#444;padding:5px 6px}
.subscribe{left:539px;top:1112px;width:101px;height:25px;background:var(--lilac);border:1px solid #9a9cd0;border-radius:2px;color:var(--white);font:700 12.5px 'Roboto',sans-serif;display:flex;align-items:center;justify-content:center}
.foot-brand{left:842px;top:1056px;display:flex;align-items:center;gap:8px;font:500 22px 'Roboto',sans-serif;color:var(--white);white-space:nowrap}
.foot-brand i{display:inline-block;width:12px;height:12px;border-radius:50%;background:var(--white)}
.copyright{left:0;top:1157px;width:1167px;height:43px;background:var(--lilac);color:var(--white);font:400 11.7px 'Roboto',sans-serif;display:flex;align-items:center;justify-content:center}
</style>
</head>
<body>

<header>
  <div class="abs topbar"></div>
  <div class="abs search">Type Word...
    <svg width="11" height="11" viewBox="0 0 12 12"><circle cx="5" cy="5" r="3.6" fill="none" stroke="#999" stroke-width="1.6"/><line x1="7.7" y1="7.7" x2="11" y2="11" stroke="#999" stroke-width="1.8"/></svg>
  </div>
  <div class="abs contact-us">CONTACT US</div>

  <div class="abs brand"><i></i>The Velda Group</div>

  <nav>
    <div class="abs nav-item active" style="left:352px">
      <svg viewBox="0 0 28 28" width="28"><path d="M14 4 3 14h3v10h6v-6h4v6h6V14h3z" fill="#3a3a3a"/></svg>HOME</div>
    <div class="abs nav-divider" style="left:428px"></div>
    <div class="abs nav-item" style="left:437px">
      <svg viewBox="0 0 28 28" width="28"><circle cx="9" cy="9" r="5" fill="none" stroke="#555" stroke-width="3" stroke-dasharray="2.5 1.5"/><circle cx="18" cy="18" r="6" fill="none" stroke="#555" stroke-width="3.5" stroke-dasharray="3 1.8"/></svg>SERVICES</div>
    <div class="abs nav-divider" style="left:523px"></div>
    <div class="abs nav-item" style="left:527px">
      <svg viewBox="0 0 32 28" width="32"><circle cx="10" cy="9" r="4" fill="#333"/><circle cx="22" cy="9" r="4" fill="#333"/><circle cx="16" cy="11" r="5" fill="#222"/><path d="M2 24c0-6 4-9 8-9s5 2 6 2 2-2 6-2 8 3 8 9z" fill="#333"/></svg>CLIENTS</div>
    <div class="abs nav-divider" style="left:609px"></div>
    <div class="abs nav-item" style="left:618px">
      <svg viewBox="0 0 28 28" width="28"><circle cx="14" cy="14" r="11.5" fill="none" stroke="#222" stroke-width="2"/><path d="M10 8c-1 1-1 3 1 6s4 5 6 5l1-2-2-2-1 1c-1-1-3-3-3-4l1-1-2-2z" fill="#222"/></svg>CONTACT</div>
    <div class="abs nav-divider" style="left:705px"></div>
    <div class="abs nav-item" style="left:708px">
      <svg viewBox="0 0 28 28" width="28"><circle cx="14" cy="13" r="6" fill="none" stroke="#333" stroke-width="1.8"/><rect x="11" y="19" width="6" height="4" fill="#333"/><g stroke="#333" stroke-width="1.5"><line x1="14" y1="2" x2="14" y2="5"/><line x1="4" y1="13" x2="7" y2="13"/><line x1="21" y1="13" x2="24" y2="13"/><line x1="7" y1="6" x2="9" y2="8"/><line x1="21" y1="6" x2="19" y2="8"/></g></svg>INSPIRE</div>
    <div class="abs nav-underline"></div>
  </nav>

  <div class="abs call">
    <svg width="14" height="14" viewBox="0 0 14 14"><path d="M3 1c-2 1-2 4 1 7s6 4 8 2l-2-3-2 1C6 7 5 6 4 4l1-2z" fill="#fff"/></svg>
    <span>Call :<b>+ 353 1 5550142</b></span>
  </div>
</header>

<section>
  <div class="abs hero" role="img" aria-label="Photo of a person in silhouette studying a large world map lit in warm orange tones"></div>
  <div class="abs hero-arrow" style="left:10px"><svg width="16" height="20" viewBox="0 0 16 20"><path d="M12 2 4 10l8 8" fill="none" stroke="#fff" stroke-width="2.2"/></svg></div>
  <div class="abs hero-arrow" style="left:1100px"><svg width="16" height="20" viewBox="0 0 16 20"><path d="M4 2l8 8-8 8" fill="none" stroke="#fff" stroke-width="2.2"/></svg></div>
  <div class="abs hero-caption">As Ireland's Largest Satelite Image Processer, We Can Provide You With<br>Background Imagery For Your Project...</div>
</section>

<main>
  <div class="abs content"></div>

  <h2 class="abs col-title" style="left:167px">About <span>The Velda Group</span></h2>
  <div class="abs col-rule" style="left:167px;width:266px"></div>
  <p class="abs copy" style="left:167px;width:268px">The VELDA Group has been in business since 1994 and continues to develop and update its range of services. The company has a high level of expertise in handling data and information, and in building and re-engineering database systems. We have a particular expertise in working with Irish data sets and have a strong grounding in dealing with spatial data.</p>
  <a class="abs more" style="left:361px">Read More &gt;&gt;</a>

  <h2 class="abs col-title" style="left:486px">Services <span>We Provide</span></h2>
  <div class="abs col-rule" style="left:486px;width:251px"></div>
  <div class="abs copy" style="left:486px;width:251px">
    <p>VELDA has extensive experience in Spatial Data processing. Services include:</p>
    <ul class="ticks">
      <li><svg width="12" height="9" viewBox="0 0 12 9"><path d="M1 4l4 4 6-7" fill="none" stroke="#233f7a" stroke-width="2"/></svg>Data Management</li>
      <li><svg width="12" height="9" viewBox="0 0 12 9"><path d="M1 4l4 4 6-7" fill="none" stroke="#233f7a" stroke-width="2"/></svg>Spatial Data</li>
      <li><svg width="12" height="9" viewBox="0 0 12 9"><path d="M1 4l4 4 6-7" fill="none" stroke="#233f7a" stroke-width="2"/></svg>Land Use</li>
      <li><svg width="12" height="9" viewBox="0 0 12 9"><path d="M1 4l4 4 6-7" fill="none" stroke="#233f7a" stroke-width="2"/></svg>Transport</li>
      <li><svg width="12" height="9" viewBox="0 0 12 9"><path d="M1 4l4 4 6-7" fill="none" stroke="#233f7a" stroke-width="2"/></svg>Consulting</li>
    </ul>
  </div>
  <a class="abs more" style="left:652px">Read More &gt;&gt;</a>

  <h2 class="abs col-title" style="left:771px">Latest <span>News</span></h2>
  <div class="abs col-rule" style="left:771px;width:231px"></div>
  <div class="abs news" style="top:660px">
    <div class="date"><div class="m">DEC</div><div class="d">22</div></div>
    <p>Lorem ipsum dolor sit Lorem amet consectetuer adipiscing elit, sed diam nonummy...</p>
  </div>
  <div class="abs news" style="top:726px">
    <div class="date"><div class="m">DEC</div><div class="d">23</div></div>
    <p>Lorem ipsum dolor sit Lorem amet consectetuer adipiscing elit, sed diam nonummy...</p>
  </div>
  <a class="abs more" style="left:937px">View All &gt;&gt;</a>

  <div class="abs dotted" style="top:839px"></div>
  <div class="abs clients-label">Our Clients :</div>
  <svg class="abs" style="left:290px;top:886px" width="14" height="22" viewBox="0 0 14 22"><path d="M12 2 3 11l9 9" fill="none" stroke="#888" stroke-width="2"/></svg>
  <div class="abs client" style="left:318px;width:106px"><i></i>Norvale</div>
  <div class="abs client" style="left:450px;width:170px">Coach Anvil</div>
  <div class="abs client" style="left:644px;width:228px">Harbour Transit</div>
  <div class="abs client" style="left:882px;width:100px;font-size:15px">Global Council</div>
  <svg class="abs" style="left:986px;top:886px" width="14" height="22" viewBox="0 0 14 22"><path d="M2 2l9 9-9 9" fill="none" stroke="#888" stroke-width="2"/></svg>
  <div class="abs dotted" style="top:949px"></div>
</main>

<footer>
  <div class="abs footer"></div>

  <h3 class="abs foot-title" style="left:167px">
    <svg width="16" height="22" viewBox="0 0 16 22"><rect x="1" y="3" width="14" height="18" fill="none" stroke="#fff" stroke-width="1.6"/><rect x="5" y="1" width="6" height="4" fill="#fff"/><g stroke="#fff"><line x1="4" y1="10" x2="12" y2="10"/><line x1="4" y1="14" x2="12" y2="14"/><line x1="4" y1="18" x2="12" y2="18"/></g></svg>Main Menu</h3>
  <ul class="abs foot-list" style="left:167px;top:1044px;line-height:20.4px">
    <li>Home</li><li>Services</li><li>Clients</li><li>Contact</li><li>Inspire</li>
  </ul>
  <div class="abs foot-divider" style="left:311px"></div>

  <h3 class="abs foot-title" style="left:348px">
    <svg width="14" height="26" viewBox="0 0 14 26"><circle cx="7" cy="6" r="5" fill="none" stroke="#fff" stroke-width="1.6"/><rect x="4" y="11" width="6" height="13" rx="3" fill="#fff"/></svg>Get In Touch</h3>
  <ul class="abs foot-list" style="left:353px;top:1043px;line-height:26.8px;font-size:12.8px">
    <li>Friendpage</li><li>Chirper</li><li>Circles+</li><li>LinkPro</li>
  </ul>
  <div class="abs foot-divider" style="left:502px"></div>

  <h3 class="abs foot-title" style="left:539px">
    <svg width="36" height="28" viewBox="0 0 36 28"><path d="M2 10 22 2l12 16-20 8z" fill="none" stroke="#fff" stroke-width="1.6"/><path d="M2 10l16 7 4-15" fill="none" stroke="#fff" stroke-width="1.4"/></svg>Subscribe to Newsletter</h3>
  <p class="abs foot-note">get latest updates by entering your email address</p>
  <div class="abs email">Email Address</div>
  <div class="abs subscribe">Subscribe</div>
  <div class="abs foot-divider" style="left:805px"></div>

  <div class="abs foot-brand"><i></i>The Velda Group</div>

  <div class="abs copyright">©2013The Velda Group . All rights reserved.</div>
</footer>

</body>
</html>
```